Group training gym/bootcamp needs a web design

We need a website for our gym that is based in Sydney. We have indoor functional training classes and outdoor bootcamp classes. We would like the web site to have a video (to be created) and photo gallery. I would like the site made on word press and i would like to be able to make minor changes such as changing images and text without having to use a designer.

The website should have the following pages: home page; the gym; the bootcamp; photo gallery; about us; contact.

I have uploaded our logo and i would like to keep to these colour (blue,yellow,silver) and black is also allowed

Target Market(s)

18-50 male and female

Industry/Entity Type

Gym

Coding

Coded - Design and coding required

Number of Pages Required

5+ page

Font styles to use
Sans Serif

Colors
0692cd
fbed22
1b1b1b
e8e8e8

Requirements
Must have
• The website should have the following pages: home page; the gym; the bootcamp; photo gallery; about us; contact.
• I have uploaded our logo and i would like to keep to these colour (blue,yellow,silver) and black is also allowed
• Video upload and photo upload

```html
<!DOCTYPE html>
<html lang="en">
<head>
<meta charset="utf-8">
<title>Ironbay Training Club</title>
<link href="https://fonts.googleapis.com/css2?family=Oswald:wght@400;500;600&family=Lato:wght@300;400;700;900&display=swap" rel="stylesheet">
<style>
:root{
  --blue:#3089c7;
  --yellow:#f0c419;
  --dark:#1b1b1b;
  --grey-bg:#f5f5f5;
  --text:#4a4a4a;
  --muted:#8a8a8a;
  --orange:#ee5a24;
  --white:#ffffff;
}
*{margin:0;padding:0;box-sizing:border-box}
html,body{width:676px;height:1200px;overflow:hidden;background:var(--white)}
body{position:relative;font-family:'Lato',sans-serif;color:var(--text)}
.abs{position:absolute}
.btn{position:absolute;display:flex;align-items:center;justify-content:center;background:var(--blue);color:var(--white);font-family:'Oswald',sans-serif;font-weight:500;font-size:11px;letter-spacing:.3px;border-radius:12px;height:25px;width:100px}

/* hero */
.hero{left:0;top:0;width:676px;height:394px;background:linear-gradient(90deg,#262626 0%,#3d3d3d 30%,#3a3a3a 70%,#1c1c1c 100%);overflow:hidden}
.hero-photo{left:0;top:0;width:676px;height:394px;background:linear-gradient(90deg,rgba(0,0,0,0) 30%,rgba(110,76,52,.55) 45%,rgba(110,76,52,.55) 65%,rgba(0,0,0,0) 82%),linear-gradient(180deg,rgba(0,0,0,.15),rgba(0,0,0,.35))}
.brand{display:flex;align-items:center;gap:6px;justify-content:center}
.brand-dot{width:14px;height:14px;border-radius:50%;background:var(--blue)}
.brand-name{font-family:'Oswald',sans-serif;font-weight:600;font-size:14px;color:var(--yellow);letter-spacing:.5px;line-height:16px}
.hero .brand{left:0;width:676px;top:30px}
.nav{left:0;width:676px;top:73px;display:flex;justify-content:center;gap:16px;font-family:'Oswald',sans-serif;font-weight:500;font-size:8.5px;line-height:10px;color:var(--white)}
.arrow{top:180px}
.hero-title{left:0;width:676px;top:166px;text-align:center;font-family:'Oswald',sans-serif;font-weight:600;font-size:37px;line-height:38px;color:var(--white);letter-spacing:.2px}
.hero-title span{color:var(--yellow)}
.hero-sub{left:0;width:676px;top:209px;text-align:center;font-weight:700;font-size:8px;line-height:10px;color:var(--white)}
.hero .btn{left:288px;top:235px}

/* about */
.about-title{left:106px;top:438px;font-weight:700;font-size:27px;line-height:28px;color:#7a7a7a}
.about-title .b{color:var(--blue)}
.about-title .y{color:var(--yellow)}
.about-text{left:106px;top:504px;width:228px;font-size:6.5px;font-weight:400;line-height:10px;color:var(--muted)}
.about .btn{left:106px;top:566px}
.about-photo{left:345px;top:428px;width:225px;height:191px;background:linear-gradient(180deg,#7a5742 0%,#5a3f2f 60%,#3f4a66 100%)}

/* featured */
.featured{left:0;top:619px;width:676px;height:217px;background:var(--grey-bg)}
.featured h2{position:absolute;left:0;width:676px;top:20px;text-align:center;font-size:20px;line-height:24px;font-weight:700;color:var(--text)}
.featured .lead{position:absolute;left:168px;width:340px;top:48px;text-align:center;font-size:6.4px;line-height:10px;color:var(--muted)}
.card{position:absolute;top:82px;width:149px;height:119px;background:var(--white)}
.card-photo{height:73px}
.card h3{position:absolute;left:8px;top:82px;font-size:7.5px;font-weight:400;color:#222}
.card p{position:absolute;left:8px;top:100px;font-size:5.5px;color:var(--muted);display:flex;align-items:center;gap:4px}
.slide-btn{position:absolute;top:129px;width:12px;height:13px;background:var(--orange);color:var(--white);font-size:8px;display:flex;align-items:center;justify-content:center}

/* promo */
.promo{left:0;top:836px;width:676px;height:232px;background:linear-gradient(90deg,#3a3a3a 0%,#2a2a2a 40%,#161616 100%)}
.promo-photo{left:0;top:0;width:300px;height:232px;background:linear-gradient(90deg,rgba(80,74,68,.55) 0%,rgba(60,56,52,.4) 55%,rgba(0,0,0,0) 100%)}
.promo h2{position:absolute;left:239px;top:54px;font-size:20px;line-height:24px;font-weight:700;color:var(--white)}
.promo .offer{position:absolute;left:239px;top:84px;font-size:20px;font-weight:300;line-height:24px;color:var(--white)}
.promo .offer span{color:var(--yellow)}
.promo .btn{left:237px;top:142px}

/* footer */
.footer .brand{left:0;width:676px;top:1112px}
.social{left:0;width:676px;top:1145px;display:flex;justify-content:center;gap:6px}
.social i{width:12px;height:12px;border:1px solid #333;border-radius:50%;display:block}
.copy{left:0;width:676px;top:1165px;text-align:center;font-size:7px;color:var(--muted)}
.bar{left:0;top:1194px;width:676px;height:6px;background:var(--blue)}
</style>
</head>
<body>

<section class="hero abs">
  <div class="hero-photo abs" role="img" aria-label="Muscular athlete curling a dumbbell in a dim gym"></div>
  <div class="brand abs"><span class="brand-dot"></span><span class="brand-name">IRONBAY TRAINING CLUB</span></div>
  <nav class="nav abs"><span>HOME</span><span>THE GYM</span><span>THE BOOTCAMP</span><span>PHOTO GALLERY</span><span>ABOUT US</span><span>CONTACT</span></nav>
  <svg class="arrow abs" style="left:58px" width="12" height="22" viewBox="0 0 12 22"><path d="M10 2 2 11l8 9" fill="none" stroke="#fff" stroke-width="2"/></svg>
  <svg class="arrow abs" style="left:600px" width="12" height="22" viewBox="0 0 12 22"><path d="M2 2l8 9-8 9" fill="none" stroke="#fff" stroke-width="2"/></svg>
  <h1 class="hero-title abs">BUILD YOUR <span>BODY</span> STRONG</h1>
  <p class="hero-sub abs">READY TO CHANGE YOUR PHYSIQUE, BUT CAN'T WORK OUT IN THE GYM?</p>
  <a class="btn">JOIN WITH US</a>
</section>

<section class="about">
  <h2 class="about-title abs">ALL ABOUT<br><span class="b">GYM</span> <span class="y">FITNESS</span></h2>
  <p class="about-text abs">Lorem ipsum dolor sit amet, consectetur adipiscing elit, sed do eiusmod tempor incididunt ut labore et dolore magna aliqua. Ut enim ad minim veniam, quis nostrud exerc esse cillum dolore Lorem ipsum dolor sit amet, consectetur adipiscing elit, sed do eiusmod tempor incididunt ut labore et</p>
  <a class="btn">SING UP</a>
  <div class="about-photo abs" role="img" aria-label="Athlete seen from behind flexing both arms"></div>
</section>

<section class="featured abs">
  <h2>FEATURED CLASSES</h2>
  <p class="lead">Lorem ipsum dolor sit amet, consectetur adipisicing elit. Consequuntur, libero sed cum. Delectus suscipit tempore fugit, accusamus inventore, sunt quod ullam saepe consequuntur quasi illo odit</p>
  <span class="slide-btn" style="left:94px">‹</span>
  <div class="card" style="left:108px">
    <div class="card-photo" role="img" aria-label="Women lifting dumbbells overhead" style="background:linear-gradient(135deg,#d6d2ce,#9a8e86)"></div>
    <h3>Cycling</h3><p><svg width="5" height="6" viewBox="0 0 5 6"><circle cx="2.5" cy="1.5" r="1.4" fill="#777"/><path d="M0 6a2.5 2.5 0 0 1 5 0z" fill="#777"/></svg>Mara Quill, Tessa Rowe</p>
  </div>
  <div class="card" style="left:265px">
    <div class="card-photo" role="img" aria-label="Men training with dumbbells in a gym" style="background:linear-gradient(135deg,#7a7673,#34312f)"></div>
    <h3>Martial Arts</h3><p><svg width="5" height="6" viewBox="0 0 5 6"><circle cx="2.5" cy="1.5" r="1.4" fill="#777"/><path d="M0 6a2.5 2.5 0 0 1 5 0z" fill="#777"/></svg>Owen Hartley, Liam Becker</p>
  </div>
  <div class="card" style="left:421px">
    <div class="card-photo" role="img" aria-label="Trainer assisting a woman on a bench press" style="background:linear-gradient(135deg,#4a6aa8,#c44a44)"></div>
    <h3>Running</h3><p><svg width="5" height="6" viewBox="0 0 5 6"><circle cx="2.5" cy="1.5" r="1.4" fill="#777"/><path d="M0 6a2.5 2.5 0 0 1 5 0z" fill="#777"/></svg>Nadia Ferro, Ravi Stone, Liam Becker</p>
  </div>
  <span class="slide-btn" style="left:573px">›</span>
</section>

<section class="promo abs">
  <div class="promo-photo abs" role="img" aria-label="Runner's legs on a treadmill"></div>
  <h2>FITNESS CLASSES THIS SUMMER</h2>
  <p class="offer">PAY NOW AND<br><span>GET 35%</span> DISCOUNT</p>
  <a class="btn">BECOME A MEMBER</a>
</section>

<footer class="footer">
  <div class="brand abs"><span class="brand-dot"></span><span class="brand-name">IRONBAY TRAINING CLUB</span></div>
  <div class="social abs"><i></i><i></i><i></i><i></i></div>
  <p class="copy abs">Copyright © Ironbay Training Club 2017. All Rights Reserved | Privacy Policy | Terms of Use</p>
  <div class="bar abs"></div>
  <svg class="abs" style="left:318px;top:1182px" width="40" height="12" viewBox="0 0 40 12"><path d="M0 12 20 0l20 12z" fill="var(--blue)"/></svg>
</footer>

</body>
</html>
```